New Webpage for High Class Expert Witness Services Company

We are looking for a minimalist design for a webpage that just has our logo and an entry form offer to connect with one of our Liaisons.
The entry form should just ask for Name, Email, Contact Info and Description of Project.

Company Name is: The Marlowe Crest Advisory Services

Number of Pages Required

1 page

```html
<!DOCTYPE html>
<html lang="en">
<head>
<meta charset="utf-8">
<title>Connect Now – The Marlowe Crest Advisory Services</title>
<link href="https://fonts.googleapis.com/css2?family=Cinzel:wght@500&family=Poppins:wght@400;500;600&display=swap" rel="stylesheet">
<style>
  :root{
    --stage:#474747;
    --bar-light:#1b1b1b;
    --bar-dark:#1c1c1c;
    --page-light:#fcf3f1;
    --page-dark:#141414;
    --ink-light:#1a1a1a;
    --ink-dark:#ffffff;
    --field-light:#ffffff;
    --field-line-dark:#3e3e3e;
    --copper:#b07548;
    --footer-ink:#e9e9e9;
    --name-ink:#e8e8e8;
  }
  *{box-sizing:border-box;margin:0;padding:0}
  html,body{width:1200px;height:525px;overflow:hidden;background:var(--stage)}
  body{position:relative;font-family:'Poppins',sans-serif}

  .page{position:absolute;top:65px;width:519px;height:396px;overflow:hidden;box-shadow:0 4px 14px rgba(0,0,0,.25)}
  .page--light{left:56px;background:var(--page-light);color:var(--ink-light)}
  .page--dark{left:625px;background:var(--page-dark);color:var(--ink-dark)}

  .site-header{position:absolute;left:0;top:0;width:100%;height:48px;display:flex;align-items:center;justify-content:center;gap:7px}
  .page--light .site-header{background:var(--bar-light)}
  .page--dark .site-header{background:var(--bar-dark);height:56px;border-bottom:1px solid #262626}
  .brand-mark{width:9px;height:9px;background:var(--copper)}
  .brand-name{font-family:'Cinzel',serif;font-weight:500;font-size:11px;letter-spacing:.06em;color:var(--name-ink);text-transform:uppercase}
  .page--dark .brand-name{font-size:12px}

  .connect{position:absolute;left:0;width:100%;text-align:center}
  .connect__title{position:absolute;left:0;top:115px;width:100%;font-family:'Cinzel',serif;font-weight:500;font-size:25px;letter-spacing:.02em;line-height:30px}
  .connect__rule{position:absolute;left:241px;top:144px;width:37px;height:1.5px;background:var(--copper)}
  .connect__lead{position:absolute;left:0;top:157px;width:100%;font-size:8.8px;line-height:13px}
  .connect__note{position:absolute;left:70px;top:176px;width:379px;font-size:8.8px;line-height:12.5px}
  .page--dark .connect__title{top:113px}
  .page--dark .connect__rule{top:142px}
  .page--dark .connect__lead{top:155px}
  .page--dark .connect__note{top:174px}

  .field{position:absolute;display:flex;align-items:center;border-radius:12px;font-size:7.3px;font-weight:500}
  .field--line{left:78px;width:177px;height:22px}
  .field--area{left:262px;top:217px;width:178px;height:78px;align-items:flex-start;padding-top:6px}
  .page--light .field{background:var(--field-light);box-shadow:0 0 4px rgba(0,0,0,.04)}
  .page--dark .field{border:1px solid var(--field-line-dark);background:transparent}
  .field__icon{width:23px;display:flex;justify-content:center;align-items:center;height:12px;border-right:1px solid #d9d9d9}
  .page--dark .field__icon{border-right-color:#3e3e3e}
  .field__icon svg{width:6px;height:6px;fill:var(--copper)}
  .field__label{padding-left:6px}
  .row-1{top:217px}.row-2{top:246px}.row-3{top:274px}
  .page--dark .row-1,.page--dark .field--area{top:215px}
  .page--dark .row-2{top:244px}.page--dark .row-3{top:272px}

  .submit{position:absolute;left:205px;top:306px;width:110px;height:21px;background:var(--copper);color:#fff;font-weight:600;font-size:7.3px;letter-spacing:.02em;display:flex;align-items:center;justify-content:center}
  .page--dark .submit{top:304px}

  .site-footer{position:absolute;left:0;bottom:0;width:100%;height:28px;display:flex;align-items:center;justify-content:center;font-size:6.3px;color:var(--footer-ink)}
  .page--light .site-footer{background:var(--bar-light)}
  .page--dark .site-footer{background:#1e1e1e}
</style>
</head>
<body>

<section class="page page--light">
  <header class="site-header"><span class="brand-mark"></span><span class="brand-name">Marlowe Crest Advisory Services</span></header>
  <div class="connect">
    <h1 class="connect__title">CONNECT NOW</h1>
    <div class="connect__rule"></div>
    <p class="connect__lead">Direct access to experienced professionals for your mission-critical projects.</p>
    <p class="connect__note">Share a few details about your project, and a member of our team will reach out to discuss how we can support your objectives.</p>
  </div>
  <div class="field field--line row-1"><span class="field__icon"><svg viewBox="0 0 10 10"><circle cx="5" cy="3" r="2.4"/><path d="M1 10c0-3 1.8-4.3 4-4.3S9 7 9 10z"/></svg></span><span class="field__label">Your Name</span></div>
  <div class="field field--line row-2"><span class="field__icon"><svg viewBox="0 0 10 10"><path d="M0 2h10v1L5 6 0 3z"/><path d="M0 4.2 5 7.2l5-3V9H0z"/></svg></span><span class="field__label">Email</span></div>
  <div class="field field--line row-3"><span class="field__icon"><svg viewBox="0 0 10 10"><path d="M2 0.5 3.8 2.6 2.8 4c.7 1.4 1.8 2.5 3.2 3.2l1.4-1 2.1 1.8-1.2 1.6C4.5 9.4.6 5.5.4 1.7z"/></svg></span><span class="field__label">Phone</span></div>
  <div class="field field--area"><span class="field__icon"><svg viewBox="0 0 10 10"><path d="M0 1h6.5v4.5H2.5L0 7.5z"/><path d="M7.5 3H10v6L8 7.5H3.5v-1h4z"/></svg></span><span class="field__label">Project Description</span></div>
  <div class="submit">SUBMIT REQUEST</div>
  <footer class="site-footer">Copyright © 2026 The Marlowe Crest Advisory Services&nbsp; | &nbsp;All Rights Reserved</footer>
</section>

<section class="page page--dark">
  <header class="site-header"><span class="brand-mark"></span><span class="brand-name">Marlowe Crest Advisory Services</span></header>
  <div class="connect">
    <h1 class="connect__title">CONNECT NOW</h1>
    <div class="connect__rule"></div>
    <p class="connect__lead">Direct access to experienced professionals for your mission-critical projects.</p>
    <p class="connect__note">Share a few details about your project, and a member of our team will reach out to discuss how we can support your objectives.</p>
  </div>
  <div class="field field--line row-1"><span class="field__icon"><svg viewBox="0 0 10 10"><circle cx="5" cy="3" r="2.4"/><path d="M1 10c0-3 1.8-4.3 4-4.3S9 7 9 10z"/></svg></span><span class="field__label">Your Name</span></div>
  <div class="field field--line row-2"><span class="field__icon"><svg viewBox="0 0 10 10"><path d="M0 2h10v1L5 6 0 3z"/><path d="M0 4.2 5 7.2l5-3V9H0z"/></svg></span><span class="field__label">Email</span></div>
  <div class="field field--line row-3"><span class="field__icon"><svg viewBox="0 0 10 10"><path d="M2 0.5 3.8 2.6 2.8 4c.7 1.4 1.8 2.5 3.2 3.2l1.4-1 2.1 1.8-1.2 1.6C4.5 9.4.6 5.5.4 1.7z"/></svg></span><span class="field__label">Phone</span></div>
  <div class="field field--area"><span class="field__icon"><svg viewBox="0 0 10 10"><path d="M0 1h6.5v4.5H2.5L0 7.5z"/><path d="M7.5 3H10v6L8 7.5H3.5v-1h4z"/></svg></span><span class="field__label">Project Description</span></div>
  <div class="submit">SUBMIT REQUEST</div>
  <footer class="site-footer">Copyright © 2026 The Marlowe Crest Advisory Services&nbsp; | &nbsp;All Rights Reserved</footer>
</section>

</body>
</html>
```